SkyvornQ Business Cards and Stationary Design

Need a design for our business cards and stationary. I want to carry on the theme of the logo. I want the business cards to have a design on the back. I would like the business cards and the stationary to carry the same theme, design scheme, and branding

Target Market(s)

Airlines and Maintenance Facilities

Industry/Entity Type

Aviation

Contact Information for Business Card

Name
Position Title
Address: 4827 Trellis Hollow Road, Fort Pierce, Florida, 34951
Office Number
Mobile Number
Email
Website

Font styles to use
Serif
Sans Serif

Colors

Designer to choose colors to be used in the design.

```html
<!DOCTYPE html>
<html lang="en">
<head>
<meta charset="UTF-8">
<title>SkyvornQ Business Cards</title>
<link href="https://fonts.googleapis.com/css2?family=Source+Sans+3:wght@300;400;600;700;800&display=swap" rel="stylesheet">
<style>
  :root {
    --navy: #1b2b57;
    --band-navy: #1f3470;
    --sky: #2a9ad8;
    --ink: #3a3d45;
    --muted: #5f6168;
    --divider: #c9cbcf;
    --card: #ffffff;
    --card-edge: #c4c6ca;
    --bg-light: #ebeced;
    --bg-dark: #d3d5d7;
  }
  * { margin: 0; padding: 0; box-sizing: border-box; }
  html, body { width: 1200px; height: 1104px; overflow: hidden; }
  body {
    position: relative;
    background: linear-gradient(135deg, var(--bg-light), var(--bg-dark));
    font-family: "Source Sans 3", sans-serif;
    color: var(--ink);
  }
  .card {
    position: absolute;
    background: var(--card);
    border: 1px solid var(--card-edge);
    border-radius: 28px;
    overflow: hidden;
  }
  .card-front { left: 77px; top: 61px; width: 763px; height: 435px; }
  .card-back { left: 383px; top: 552px; width: 761px; height: 436px; }

  .brand-ring {
    position: absolute;
    border-radius: 50%;
    border: 7px solid var(--navy);
  }
  .brand-name {
    position: absolute;
    font-weight: 800;
    color: var(--navy);
    text-align: center;
    white-space: nowrap;
    line-height: 1;
  }
  .card-front .brand-ring { left: 186px; top: 111px; width: 100px; height: 100px; }
  .card-front .brand-name { left: 0; width: 472px; top: 226px; font-size: 41px; letter-spacing: 0.2em; padding-left: 0.2em; }

  .divider { position: absolute; left: 434px; top: 98px; width: 2px; height: 184px; background: var(--divider); }

  .person { position: absolute; left: 460px; top: 93px; }
  .person-name { font-weight: 700; font-size: 28px; color: var(--navy); letter-spacing: 0.01em; line-height: 1.15; }
  .person-title { font-weight: 300; font-size: 25px; color: var(--muted); line-height: 1.2; }

  .contact-list { position: absolute; left: 460px; top: 170px; list-style: none; }
  .contact-list li { display: flex; align-items: center; gap: 6px; height: 27px; font-size: 20px; color: var(--ink); }
  .contact-list svg { width: 18px; height: 18px; flex: none; }

  .rule { position: absolute; left: 0; width: 100%; height: 2px; background: var(--band-navy); }
  .rule-top { top: 349px; }
  .rule-bottom { top: 399px; }
  .address-band {
    position: absolute; left: 0; top: 354px; width: 100%; height: 42px;
    background: linear-gradient(90deg, var(--band-navy) 15%, var(--sky) 50%, var(--band-navy) 85%);
    display: flex; align-items: center; justify-content: center; gap: 7px;
    color: #fff; font-size: 18px;
  }
  .address-band svg { width: 17px; height: 17px; }

  .card-back .brand-ring { left: 310px; top: 95px; width: 138px; height: 138px; border-width: 9px; }
  .card-back .brand-name { left: 0; width: 100%; top: 259px; font-size: 52px; letter-spacing: 0.3em; padding-left: 0.3em; }
  .back-url {
    position: absolute; left: 0; width: 100%; top: 356px;
    text-align: center; font-size: 25px; letter-spacing: 0.26em; padding-left: 0.26em;
    color: var(--ink);
  }
</style>
</head>
<body>
  <section class="card card-front">
    <div class="brand-ring"></div>
    <div class="brand-name">SKYVORNQ</div>
    <div class="divider"></div>
    <div class="person">
      <div class="person-name">DARREN COLWICK</div>
      <div class="person-title">PRESIDENT</div>
    </div>
    <ul class="contact-list">
      <li>
        <svg viewBox="0 0 20 20" fill="none" stroke="#1b2b57" stroke-width="1.6"><circle cx="10" cy="10" r="8.5"/><path d="M7 5.5l1.6 2.2-1 1.2c.6 1.3 1.5 2.2 2.8 2.8l1.2-1 2.2 1.6-1 1.6c-3.2-.3-6.4-3.5-6.7-6.7z" fill="#1b2b57" stroke="none"/></svg>
        772-555-0148
      </li>
      <li>
        <svg viewBox="0 0 20 20" fill="none" stroke="#1b2b57" stroke-width="1.6"><circle cx="10" cy="10" r="8.5"/><rect x="7" y="5" width="6" height="10" rx="1.2"/></svg>
        772-555-0193
      </li>
      <li>
        <svg viewBox="0 0 20 20" fill="none" stroke="#1b2b57" stroke-width="1.6"><circle cx="10" cy="10" r="8.5"/><rect x="5.5" y="7" width="9" height="6.5" rx="0.8"/><path d="M5.5 7.5l4.5 3.3 4.5-3.3"/></svg>
        info@skyvornq.com
      </li>
      <li>
        <svg viewBox="0 0 20 20" fill="none" stroke="#1b2b57" stroke-width="1.4"><circle cx="10" cy="10" r="8.5"/><ellipse cx="10" cy="10" rx="3.8" ry="8.5"/><path d="M1.5 10h17M3 5.5h14M3 14.5h14"/></svg>
        www.skyvornq.com
      </li>
    </ul>
    <div class="rule rule-top"></div>
    <div class="address-band">
      <svg viewBox="0 0 20 20" fill="none" stroke="#fff" stroke-width="1.6"><circle cx="10" cy="10" r="8.5"/><path d="M10 15s-3.5-3.6-3.5-6a3.5 3.5 0 0 1 7 0c0 2.4-3.5 6-3.5 6z"/><circle cx="10" cy="9" r="1.2"/></svg>
      4827 Trellis Hollow Road, Fort Pierce, Florida, 34951
    </div>
    <div class="rule rule-bottom"></div>
  </section>

  <section class="card card-back">
    <div class="brand-ring"></div>
    <div class="brand-name">SKYVORNQ</div>
    <div class="back-url">www.skyvornq.com</div>
  </section>
</body>
</html>
```